Home Loan Introducer needs logo/business cards

We need a simple but classy logo for business cards and flyers. The business is a home loan referral business that is called an Introducer. The business name is "The Harborline".
I was thinking very simple and straight to the point on the front with "Home Loans" the only thing on the front with a nice background colour/s.
Then on the back, "The Harborline"
and "Quality Customer Service"
and "Email, text or call welcome"
and then my name, email address and phone number.
Updates
Thank you for all the designs :-)
Target Market(s)
Home buyers.
Home owners.
Investors.
Industry/Entity Type
Loan
Look and feel

```html
<!DOCTYPE html>
<html lang="en">
<head>
<meta charset="UTF-8">
<title>The Harborline – Business Card</title>
<link rel="stylesheet" href="https://fonts.googleapis.com/css2?family=Roboto+Mono:wght@500;700&display=swap">
<style>
  :root {
    --page-bg: #ffffff;
    --card-bg: #0a0a0a;
    --ink-blue: #1010b8;
    --ink-soft: #3a3ad0;
  }
  * { margin: 0; padding: 0; box-sizing: border-box; }
  html, body {
    width: 1200px;
    height: 750px;
    overflow: hidden;
    background: var(--page-bg);
  }
  .canvas {
    position: relative;
    width: 1200px;
    height: 750px;
  }
  .card {
    position: absolute;
    left: 291px;
    width: 593px;
    height: 305px;
    background: var(--card-bg);
    overflow: hidden;
    font-family: "Roboto Mono", monospace;
  }
  .card--front { top: 45px; }
  .card--back { top: 378px; }
  .card-title {
    position: absolute;
    font-weight: 700;
    color: var(--ink-blue);
    line-height: 1;
    white-space: nowrap;
  }
  .card-title--front {
    left: 125px;
    top: 120px;
    font-size: 50px;
    letter-spacing: 2px;
  }
  .card-title--back {
    left: 93px;
    top: 128px;
    font-size: 40px;
    letter-spacing: 2px;
  }
  .tagline {
    position: absolute;
    left: 95px;
    top: 180px;
    font-size: 16px;
    font-weight: 500;
    letter-spacing: 1px;
    color: var(--ink-blue);
    white-space: nowrap;
  }
  .contact {
    position: absolute;
    left: 95px;
    top: 214px;
    list-style: none;
    font-size: 13px;
    font-weight: 500;
    line-height: 18px;
    color: var(--ink-soft);
    white-space: nowrap;
  }
  .contact-note { font-style: normal; margin-bottom: 4px; color: var(--ink-blue); }
  .corner-flourish {
    position: absolute;
    right: 0;
    bottom: 0;
    width: 153px;
    height: 188px;
  }
</style>
</head>
<body>
  <main class="canvas">
    <section class="card card--front">
      <h1 class="card-title card-title--front">Home Loans</h1>
    </section>
    <section class="card card--back">
      <h2 class="card-title card-title--back">The Harborline</h2>
      <p class="tagline">Quality Customer Service</p>
      <ul class="contact">
        <li class="contact-note">Email, text or call welcome</li>
        <li class="contact-name">Jordan Ellis</li>
        <li class="contact-email">jordan@harborline.example</li>
        <li class="contact-phone">0400 123 456</li>
      </ul>
      <svg class="corner-flourish" viewBox="0 0 153 188" role="img" aria-label="Blue leafy flourish ornament in the lower right corner">
        <defs>
          <radialGradient id="flourish-glow" cx="100%" cy="100%" r="100%">
            <stop offset="0%" stop-color="#1010b8" stop-opacity="0.9"/>
            <stop offset="100%" stop-color="#1010b8" stop-opacity="0"/>
          </radialGradient>
        </defs>
        <rect width="153" height="188" fill="url(#flourish-glow)"/>
      </svg>
    </section>
  </main>
</body>
</html>
```